Vantro cards

I am in the auto motive, transportation business I would like a business card that is Something cool, modern edgy, having to do with car culture. I offer towing service for high and exotic cars. I also provide towing for collisions and car accidents. I offer open and enclosed transport nationwide.

Target Market(s)

Car culture people high end auto collectors

Industry/Entity Type

Towing car carrier

Contact Information for Business Card

My company colors black yellow and silver

Font styles to use
Serif

```html
<!DOCTYPE html>
<html lang="en">
<head>
<meta charset="utf-8">
<title>Vantro Transportation — Business Cards</title>
<link href="https://fonts.googleapis.com/css2?family=Archivo:wght@400;700;900&display=swap" rel="stylesheet">
<style>
  :root {
    --backdrop: #1d1d1d;
    --card-yellow: #f9df5f;
    --card-black: #050505;
    --card-white: #ffffff;
    --ink: #0a0a0a;
    --band-text: #ffffff;
  }
  * { margin: 0; padding: 0; box-sizing: border-box; }
  html, body { width: 1200px; height: 1015px; overflow: hidden; }
  body {
    background: var(--backdrop);
    font-family: "Archivo", Arial, sans-serif;
    position: relative;
  }
  .card {
    position: absolute;
    left: 220px;
    width: 760px;
    height: 434px;
    overflow: hidden;
    background: var(--card-yellow);
    box-shadow: 0 14px 34px rgba(0,0,0,.55);
  }
  .card--front { top: 48px; }
  .card--back  { top: 532px; }

  .card__band {
    position: absolute;
    left: 0; right: 0;
    top: 306px;
    height: 46px;
    background: var(--card-black);
  }
  .card__url {
    position: absolute;
    top: 306px;
    height: 46px;
    line-height: 46px;
    color: var(--band-text);
    font-size: 19px;
    letter-spacing: 2px;
  }

  /* front */
  .brand {
    position: absolute;
    left: 0; right: 0;
    top: 118px;
    display: flex;
    align-items: center;
    justify-content: center;
    gap: 18px;
    color: var(--ink);
    font-weight: 900;
    font-size: 78px;
    letter-spacing: 4px;
  }
  .brand__square {
    width: 40px; height: 40px;
    background: var(--ink);
  }
  .card--front .card__url { left: 0; right: 0; text-align: center; }

  /* back */
  .card__white-panel {
    position: absolute;
    left: 0; top: 0; bottom: 0;
    width: 365px;
    background: var(--card-white);
  }
  .card--back .brand {
    left: 0; right: auto;
    width: 365px;
    top: 110px;
    font-size: 56px;
    gap: 12px;
    letter-spacing: 3px;
  }
  .card--back .brand__square { width: 30px; height: 30px; }
  .card--back .card__url { left: 0; width: 560px; text-align: right; }

  .contact {
    position: absolute;
    left: 405px;
    top: 70px;
    color: var(--ink);
  }
  .contact__name {
    font-weight: 700;
    font-size: 25px;
    letter-spacing: .5px;
    text-transform: uppercase;
  }
  .contact__title { font-size: 18px; margin-bottom: 18px; }
  .contact__line {
    display: flex;
    align-items: center;
    gap: 8px;
    font-size: 19px;
    line-height: 1.35;
  }
  .contact__line svg { width: 16px; height: 16px; flex: none; }
  .contact__address {
    margin-top: 14px;
    padding-left: 24px;
    font-size: 19px;
    line-height: 1.3;
  }
</style>
</head>
<body>

  <section class="card card--front" aria-label="Business card front">
    <div class="brand">
      <span class="brand__square"></span>
      <span class="brand__name">VANTRO</span>
    </div>
    <div class="card__band"></div>
    <div class="card__url">www.vantrotow.com</div>
  </section>

  <section class="card card--back" aria-label="Business card back">
    <div class="card__white-panel"></div>
    <div class="brand">
      <span class="brand__square"></span>
      <span class="brand__name">VANTRO</span>
    </div>

    <div class="contact">
      <div class="contact__name">Marcus Reyland</div>
      <div class="contact__title">Managing Director</div>
      <div class="contact__line">
        <svg viewBox="0 0 24 24" aria-hidden="true"><path fill="currentColor" d="M6.6 10.8a15.1 15.1 0 0 0 6.6 6.6l2.2-2.2c.3-.3.7-.4 1-.2 1.1.4 2.3.6 3.6.6.6 0 1 .4 1 1V20c0 .6-.4 1-1 1A17 17 0 0 1 3 4c0-.6.4-1 1-1h3.5c.6 0 1 .4 1 1 0 1.3.2 2.5.6 3.6.1.3 0 .7-.2 1z"/></svg>
        <span>044-555 018 274</span>
      </div>
      <div class="contact__line">
        <svg viewBox="0 0 24 24" aria-hidden="true"><path fill="currentColor" d="M2 5h20v14H2zm2 2v.5l8 5 8-5V7zm0 2.9V17h16V9.9l-8 5z"/></svg>
        <span>info@vantrotow.com</span>
      </div>
      <div class="contact__address">
        72, Kessler Mill Lane<br>
        61820, Northland
      </div>
    </div>

    <div class="card__band"></div>
    <div class="card__url">www.vantrotow.com</div>
  </section>

</body>
</html>
```